Store Front Window Design

We have a beautiful corner store front dental practice with no window signage. Crazy I know...that's why we need your help.

The final design will be done in all vinyl unless unless you suggest a different medium (meaning we are open to some design idea like using frosted glass, etc...).

The windows provide a lot of natural light so the design needs to keep a lot of natural light coming into the office. Keep in mind vinyl is not opaque so keep the signage aesthetically pleasing and a minimalist design to allow as much natural light in as possible. The design should follow the aesthetic from our logo. or tie into at least. We want a cohesive brand aesthetic.

I submitted some general layout ideas. There is a blue banner with advertising words which we want to be used in the final version. Even though the lettering is black, in reality the letters will be a white vinyl on the outside of the window. When you submit your work, be sure to add any special instructions (aka tell me the vision for the letters is white not black, maybe gold leaf, or forested glass...stuff like that). AND YOU DO NOT HAVE TO FOLLOW MY PATTERN! YOU ARE ARTISTS AND WE ARE LOOKING FOR AN ARTISTIC EYE CATCHING PRESENTATION OF THIS INFORMATION. MAKE IT FLASHY AND ADD SOME AESTHETIC FROM THE TOOTH LOGO.

The store front is 6 windows roughly 60'' x 36'' The smaller windows below are 27'' x 36''. Around the corner there are 3 windows. they are 60'' x 27'' lower windows are 27" x 27". We would like to keep the bottom windows clear and keep the signage on the top windows, however, we are flexible.

The front 6 windows need to have this information worked into the design.

Practice name: Varden and Pellosi Dental & Orthodontics.
Phone numbers: Rosalind Varden DDS: 415.555.0187
Oskar Pellosi DDS:415.555.0243

Expertise: Dr. Varden General Dentistry & Orthodontics
Dr. Pellosi Oral Surgery & Sedation

Address: 1938 Birchwood Ave

A banner across the bottom of the top windows with some key advertisement words: "Clearmold" "Braces" "Implants" "Whiting" "Call today" "Free Consultation" "Oral Surgery" "Sedation". We like the two color idea. Its up to you to decide on the color combo. I used a Dark and light blue, but maybe a Blue and grey would nice to tire in the logo colors?

I have made some mock ideas to get the ball rolling but you do not have to stick to these designs at all, just as long as all the required information is there. Be creative with the layouts, fonts, color scheme, (just remember these are going on windows not necessarily a white background), and graphics/artistic flare (refer to logo for layout inspiration and use the logo as an actual graphic). We are running a miltimillion dollar dental practice so we want these windows to be eye catching to pull in patients and look like a million dollar design. Also all 6 windows dont need ot be used. I am really looking for creative design marketing.

The corner 3 windows need the following information: name, expertise, phone number, banner.

Dr. Varden, General Dentistry & Orthodontics, 415.555.0187
Dr. Pellosi, Oral Surgery & Sedation, 415.555.0243

There is also a front door that needs to be designed. The door is 60'' x 36'' (standard door size) We want simple white vinyl on the outside of the door. We need you to organize the information on the door, pick a easy to read font, maybe use the logo and use some of the front window signage aesthetic? Its up to you...but we we were initially thinking of just making the litters white and keep it simple but again you are the designers.

Practice name: Varden and Pellosi General Dentistry & Orthodontics

Address: 1938 Birchwood Ave

Phone numbers: Dr. Varden 415.555.0187
Dr. Pellosi 415.555.0243

Hours of operation: Mon: call for an appointment
Tues-Thurs: 9am-5pm
Sat: call for an appointment
Sun: Closed

A line saying we speak Spanish: Se Habla Espanol

*****************************************************************************************************
here are some design that we liked and some rough sketches I made to start the ball rolling. Keep in mind that there are 9 windows for the front because its a corner office, but not all of them have to have stuff on it. We want simple, streamline, classy high commanding price point aesthetic. I am hiring you for your artistic minds.

Target Market(s)

anyone who has dental needs

Industry/Entity Type

Dental

Font styles to use
Serif
Sans Serif

Colors

Designer to choose colors to be used in the design.

Requirements
Must have
• 1. The required information (see project description)
• 2. Logo
• 3. Advertisement banner running along the bottom of all 9 windows (6 in front and 3 on the side)
• NOTE: Look at pictures of the store to get a sense of the customers point of view and also as a reference to how your design will be broken up across several windows or maybe you design something special for every window. But we want the banner to run along all the windows to lead customs to the door on the side. Finally the letters will be done in white vinyl unless state otherwise, remember the window needs to let in natural light so the entire window can not be covered in vinyl.
Nice to have
• artistic flare yet simple and sleep and expensive looking aesthetic. work logo into the design.
Should not have
• The goal is to catch someone eye and give them important information about the practice.
• It should not just be words.
• It should not have to many words
• It must be readable font for cards driving by.

```html
<!DOCTYPE html>
<html lang="en">
<head>
<meta charset="utf-8">
<title>Varden and Pellosi Dental &amp; Orthodontics – Door Signage</title>
<link rel="stylesheet" href="https://fonts.googleapis.com/css2?family=Montserrat:wght@400;500;600;700&family=Roboto+Condensed:wght@700&display=swap">
<style>
  :root {
    --backdrop: #efefef;
    --panel: #333333;
    --ink-light: #ffffff;
    --ink-dark: #333333;
    --band: #ffffff;
  }
  * { margin: 0; padding: 0; box-sizing: border-box; }
  html, body {
    width: 1200px; height: 1200px; overflow: hidden;
    background: var(--backdrop);
    font-family: "Montserrat", Arial, sans-serif;
  }
  .door {
    position: absolute; left: 238px; top: 0;
    width: 722px; height: 1200px;
    background: var(--panel);
    color: var(--ink-light);
  }
  .door > * { position: absolute; line-height: 1; white-space: nowrap; }
  .brand-mark {
    left: 321px; top: 62px; width: 80px; height: 80px;
    border: 3px solid var(--ink-light); border-radius: 50%;
  }
  .brand-name {
    left: 0; width: 722px; top: 176px;
    text-align: center; font-weight: 500; font-size: 20px;
    letter-spacing: 4px; line-height: 1.25;
  }
  .address { left: 79px; top: 258px; font-size: 60px; font-weight: 700; }
  .doctor { left: 79px; font-size: 50px; font-weight: 600; }
  .doctor--varden { top: 347px; }
  .doctor--pellosi { top: 471px; }
  .phone {
    left: 79px; font-size: 40px; font-weight: 500;
    display: flex; align-items: center; gap: 14px;
  }
  .phone svg { width: 36px; height: 36px; }
  .phone--varden { top: 415px; }
  .phone--pellosi { top: 537px; }
  .divider {
    left: 79px; top: 605px; width: 555px; height: 2px;
    background: var(--ink-light);
  }
  .day { left: 78px; font-size: 40px; font-weight: 600; }
  .hours { left: 78px; font-size: 37px; font-weight: 400; }
  .day--mon { top: 621px; }
  .hours--mon { top: 671px; }
  .day--tue { top: 731px; left: 81px; }
  .hours--tue { top: 784px; left: 81px; }
  .day--sat { top: 843px; left: 79px; }
  .hours--sat { top: 893px; left: 79px; }
  .day--sun { top: 947px; left: 79px; }
  .hours--sun { top: 1001px; left: 79px; }
  .spanish-band {
    left: 0; top: 1064px; width: 722px; height: 116px;
    background: var(--band); color: var(--ink-dark);
    display: flex; align-items: center; justify-content: center;
    font-family: "Roboto Condensed", "Arial Narrow", sans-serif;
    font-weight: 700; font-size: 64px; letter-spacing: 1px;
  }
</style>
</head>
<body>
  <div class="door">
    <div class="brand-mark" aria-hidden="true"></div>
    <div class="brand-name">VARDEN AND PELLOSI<br>DENTAL &amp; ORTHODONTICS</div>

    <div class="address">1938 Birchwood Ave</div>

    <div class="doctor doctor--varden">Dr. Varden</div>
    <div class="phone phone--varden">
      <svg viewBox="0 0 36 36" aria-hidden="true">
        <circle cx="18" cy="18" r="16" fill="none" stroke="#fff" stroke-width="2.5"/>
        <path d="M13 9c-2 1-3 3-2.5 6 1 5 5 10 9 12 2.5 1 4.5 0 5.5-1.5l-3.5-3-2 1.5c-2-1-4-4-4.5-6l2-1.5L15 9z" fill="#fff"/>
      </svg>
      <span>(415)555-0187</span>
    </div>

    <div class="doctor doctor--pellosi">Dr. Pellosi</div>
    <div class="phone phone--pellosi">
      <svg viewBox="0 0 36 36" aria-hidden="true">
        <circle cx="18" cy="18" r="16" fill="none" stroke="#fff" stroke-width="2.5"/>
        <path d="M13 9c-2 1-3 3-2.5 6 1 5 5 10 9 12 2.5 1 4.5 0 5.5-1.5l-3.5-3-2 1.5c-2-1-4-4-4.5-6l2-1.5L15 9z" fill="#fff"/>
      </svg>
      <span>(415)555-0243</span>
    </div>

    <div class="divider"></div>

    <div class="day day--mon">Monday</div>
    <div class="hours hours--mon">call for an appointment</div>
    <div class="day day--tue">Tuesday-Thursday</div>
    <div class="hours hours--tue">9:00 am to 5:00 pm</div>
    <div class="day day--sat">Saturday</div>
    <div class="hours hours--sat">call for an appointment</div>
    <div class="day day--sun">Sunday</div>
    <div class="hours hours--sun">Closed</div>

    <div class="spanish-band">Se Habla Espanol</div>
  </div>
</body>
</html>
```